My Coffee beans packaging design

Our company named Harbor Bean,We are a new coffee Roasters in CHINA. We need a packaging design for our new coffee beans we roasted.We would like to see designs that use bright color. The final design should communicate the professional and modern sense.We want to catch customers eyes.We would like it is outstanding.It is a freestyle design project.We would like to see different styles.Thank you for reading our requirement.
Updates

Project Deadline Extended
Reason: Thank you for designing these for us,we want some more design.

Target Market(s)

All the people who love coffee

Industry/Entity Type

Coffee Shop

Font styles to use
Serif
Sans Serif
Decorative
Script

Requirements
Must have
• We do not have anything must haves.
Nice to have
• We do not have anything must haves
Should not have
• We do not have anything mustn't haves

```html
<!DOCTYPE html>
<html lang="en">
<head>
<meta charset="utf-8">
<title>Harbor Bean – Coffee Beans Label</title>
<link rel="stylesheet" href="https://fonts.googleapis.com/css2?family=Cinzel:wght@500;700&display=swap">
<style>
  :root {
    --paper: #ffffff;
    --plum: #3b2229;
    --teal: #3f8c82;
    --teal-soft: #7fb8ae;
    --roast: #8a5a2d;
    --roast-dark: #6d4321;
    --bean-light: #e9ddd0;
    --bean-mid: #c9b09a;
  }
  * { margin: 0; padding: 0; box-sizing: border-box; }
  html, body {
    width: 849px; height: 1200px; overflow: hidden;
    background: var(--paper);
  }
  .canvas {
    position: relative; width: 849px; height: 1200px;
    background: var(--paper);
  }
  .label {
    position: absolute; left: 136px; top: 178px;
    width: 586px; height: 827px;
    background: var(--bean-light);
    overflow: hidden;
  }
  .band {
    position: absolute; left: 0; width: 100%;
    background: var(--plum);
  }
  .band--top { top: 0; height: 43px; }
  .band--bottom { bottom: 0; height: 90px; display: flex; align-items: center; justify-content: center; }
  .bean-photo {
    position: absolute; left: 0; top: 43px; width: 100%; height: 694px;
    background:
      radial-gradient(ellipse 230px 330px at 50% 48%, rgba(255,255,255,0.95) 0%, rgba(255,255,255,0.7) 60%, rgba(255,255,255,0) 100%),
      linear-gradient(180deg, var(--bean-mid) 0%, var(--bean-light) 50%, var(--bean-mid) 100%);
  }
  .trim {
    position: absolute; left: 0; width: 100%; height: 16px;
    background: linear-gradient(90deg, var(--teal-soft), var(--teal), var(--teal-soft), var(--teal), var(--teal-soft));
    opacity: 0.75;
  }
  .trim--top { top: 48px; }
  .trim--bottom { top: 712px; }
  .emblem {
    position: absolute; left: 166px; top: 74px;
    width: 254px; height: 338px; border-radius: 50%;
    background: var(--plum);
    border: 8px solid var(--paper);
    box-shadow: 0 0 0 2px rgba(59,34,41,0.15);
  }
  .brand {
    position: absolute; left: 0; top: 458px; width: 100%;
    text-align: center; font-family: "Cinzel", serif; color: var(--roast);
  }
  .brand__name {
    font-size: 72px; font-weight: 700; letter-spacing: 3px; line-height: 1;
  }
  .brand__sub {
    margin-top: 12px;
    display: flex; align-items: center; justify-content: center; gap: 14px;
    font-size: 36px; font-weight: 700; letter-spacing: 4px; color: var(--roast-dark);
    line-height: 1;
  }
  .brand__rule { width: 70px; height: 3px; background: var(--roast-dark); }
  .brand__dot {
    width: 60px; height: 60px; border-radius: 50%;
    background: var(--teal); margin: 26px auto 0;
  }
  .weight {
    font-family: "Cinzel", serif; font-weight: 500;
    font-size: 30px; letter-spacing: 3px; color: var(--teal);
  }
</style>
</head>
<body>
  <main class="canvas">
    <section class="label">
      <div class="band band--top"></div>
      <div class="bean-photo" role="img" aria-label="Faded photograph of roasted coffee beans with a soft white glow in the centre"></div>
      <div class="trim trim--top" role="img" aria-label="Teal decorative border pattern"></div>
      <div class="trim trim--bottom" role="img" aria-label="Teal decorative border pattern"></div>
      <div class="emblem" role="img" aria-label="Oval emblem area with an illustration of a woman enjoying a cup of coffee"></div>
      <div class="brand">
        <h1 class="brand__name">HARBOR</h1>
        <div class="brand__sub"><span class="brand__rule"></span>BEAN<span class="brand__rule"></span></div>
        <div class="brand__dot"></div>
      </div>
      <div class="band band--bottom">
        <span class="weight">200G</span>
      </div>
    </section>
  </main>
</body>
</html>
```